Simple Logo Design for Semi-Clear Plastic Frosted Card stock

Create a business card on frosted plastic. compliment existing logo elements with a tree trunk, roots, or seed at the lower half and the full logo both on the front.

Contact information will go on a solid portion of the back of this design since this card stock is semi-transparent.

It is important to consider this plastic card stock medium in your design. I found helpful tips and guides listed at vellaprint-sample.net: be careful to understand ink printed on plastic cards cannot have too much of a consistent print area or risks peeling and fine lines can easily scratch off.
Updates

2" x 3.5" 20PT Clear Plastic Business cards with Round corners Please get info or templates here: https://www.vellaprint-sample.net/product-detail/2-x-35-20pt-clear-plastic-business-cards-with-round-corners

Target Market(s)

Not for profit- religion

Industry/Entity Type

Business

Must include complementary elements to the existing logo

Font styles to use
Decorative

Colors
000000

Requirements
Must have
• Elements of community, nature and oneness. Such as: seed, roots, tree trunk, etc.
• Three lines of space on the back for Name, Title, Phone Number.
Nice to have
• I like a light use of decorative elements
Should not have
• No eyes, from faces or animals.

```html
<!DOCTYPE html>
<html lang="en">
<head>
<meta charset="utf-8">
<title>Graceful Roots – Business Card</title>
<link rel="stylesheet" href="https://fonts.googleapis.com/css2?family=Josefin+Sans:wght@400&family=Open+Sans:wght@400;600&display=swap">
<style>
  :root {
    --backdrop: #e9e8e5;
    --frost: #f3f1ef;
    --teal: #236c69;
    --leaf: #3f9a43;
    --blush: #d8b7b0;
    --paper: #ffffff;
    --ink-light: #ffffff;
  }
  * { margin: 0; padding: 0; box-sizing: border-box; }
  html, body {
    width: 1200px;
    height: 900px;
    overflow: hidden;
    background: var(--backdrop);
  }
  .canvas { position: relative; width: 1200px; height: 900px; }

  .card {
    position: absolute;
    border-radius: 14px;
    overflow: hidden;
    box-shadow: 0 2px 10px rgba(0,0,0,0.12);
  }
  .card-front {
    left: 78px; top: 35px;
    width: 587px; height: 362px;
    background: var(--frost);
  }
  .card-back {
    left: 388px; top: 505px;
    width: 567px; height: 352px;
    background: var(--paper);
  }
  .card-wave { position: absolute; inset: 0; width: 100%; height: 100%; }

  .brand-mark {
    position: absolute;
    border-radius: 50%;
    background: var(--teal);
  }
  .brand-name {
    position: absolute;
    left: 0; right: 0;
    text-align: center;
    font-family: "Josefin Sans", sans-serif;
    font-weight: 400;
    color: var(--teal);
    letter-spacing: 0;
    white-space: nowrap;
  }
  .brand-tagline {
    position: absolute;
    left: 0; right: 0;
    text-align: center;
    font-family: "Open Sans", sans-serif;
    font-weight: 400;
    color: var(--teal);
    letter-spacing: 1.4px;
    text-transform: uppercase;
    white-space: nowrap;
  }

  .card-front .brand-block { position: absolute; left: 16px; top: 0; width: 340px; height: 240px; }
  .card-front .brand-mark { width: 80px; height: 80px; left: 130px; top: 92px; }
  .card-front .brand-name { top: 174px; font-size: 33px; }
  .card-front .brand-tagline { top: 210px; font-size: 11.5px; }

  .card-back .brand-mark { width: 80px; height: 80px; left: 244px; top: 110px; }
  .card-back .brand-name { top: 208px; font-size: 33px; }
  .card-back .brand-tagline { top: 244px; font-size: 11.5px; }

  .contact {
    position: absolute;
    right: 34px; top: 242px;
    text-align: right;
    font-family: "Open Sans", sans-serif;
    color: var(--ink-light);
  }
  .contact-name { font-size: 22px; font-weight: 600; line-height: 1.2; }
  .contact-title { font-size: 14.5px; font-weight: 400; margin-top: 4px; }
  .contact-phone { font-size: 14.5px; font-weight: 400; margin-top: 22px; margin-right: 22px; }
</style>
</head>
<body>
<main class="canvas">

  <section class="card card-front" aria-label="Card front">
    <svg class="card-wave" viewBox="0 0 587 362" preserveAspectRatio="none" aria-hidden="true">
      <path d="M0 236 C 90 268, 170 282, 250 264 C 340 244, 430 190, 587 206 L587 362 L0 362 Z" fill="var(--teal)"/>
      <path d="M0 240 C 90 272, 170 286, 250 268 C 340 248, 430 194, 587 210" fill="none" stroke="var(--blush)" stroke-width="4"/>
      <path d="M0 232 C 90 264, 170 278, 250 260 C 340 240, 430 186, 587 202" fill="none" stroke="var(--leaf)" stroke-width="4"/>
    </svg>
    <div class="brand-block">
      <span class="brand-mark" aria-hidden="true"></span>
      <p class="brand-name">GRACEFUL ROOTS</p>
      <p class="brand-tagline">Wisdom, Community &amp; Harmony</p>
    </div>
    <div class="contact">
      <p class="contact-name">Daniel Hartley</p>
      <p class="contact-title">Managing Director</p>
      <p class="contact-phone">(044)-555-0182</p>
    </div>
  </section>

  <section class="card card-back" aria-label="Card back">
    <span class="brand-mark" aria-hidden="true"></span>
    <p class="brand-name">GRACEFUL ROOTS</p>
    <p class="brand-tagline">Wisdom, Community &amp; Harmony</p>
  </section>

</main>
</body>
</html>
```